Business Card Design

We provide services doing multiple jobs in the construction industry.Please note: The company name needs to be ROCK SOLID BUILDING SERVICESAttached logo was an example of what we wanted. Can you change up the colors?

Industry/Entity Type

Construction

Contact Information for Business Card

ROCK SOLID BUILDING SERVICES5401 HUDSON BEND RDAUSTIN, TX 78734(512)243-6854ROCKSOLIDBUILDINGSERVICES@GMAIL.COM

```html
<!DOCTYPE html>
<html lang="en">
<head>
<meta charset="utf-8">
<title>Pearlwood Framing Works – Business Card</title>
<link href="https://fonts.googleapis.com/css2?family=Cinzel:wght@400&family=Archivo+Narrow:wght@400&display=swap" rel="stylesheet">
<style>
  :root {
    --page-bg: #e9e9e7;
    --card-white: #ffffff;
    --accent-blue: #1d98d6;
    --band-black: #050505;
    --ink: #141414;
    --logo-navy: #2b2f6b;
    --slate: #5f7f99;
    --slate-light: #8ea6b8;
  }
  * { margin: 0; padding: 0; box-sizing: border-box; }
  html, body {
    width: 1200px; height: 817px; overflow: hidden;
    background: var(--page-bg);
  }
  .card {
    position: absolute; left: 120px; top: 134px;
    width: 960px; height: 548px;
    background: var(--card-white);
    border-top: 9px solid var(--accent-blue);
    box-shadow: 0 10px 30px rgba(0,0,0,.18);
    overflow: hidden;
  }
  .brand-mark {
    position: absolute; left: 44px; top: 240px;
    display: flex; align-items: center; gap: 12px;
    font-family: "Cinzel", serif; font-size: 19px; color: var(--logo-navy);
    letter-spacing: 1px; line-height: 1.2; white-space: nowrap;
  }
  .brand-mark .brand-square {
    width: 26px; height: 26px; background: var(--logo-navy); flex: none;
  }
  .company-name {
    position: absolute; right: 360px; top: 330px;
    font-family: "Cinzel", serif; font-weight: 400; color: var(--ink);
    font-size: 34px; line-height: 1.1; letter-spacing: 1px; text-align: right;
    white-space: nowrap;
  }
  .company-name span { display: block; }
  .divider {
    position: absolute; left: 622px; top: 300px;
    width: 1.5px; height: 170px; background: var(--ink);
  }
  .contact {
    position: absolute; left: 420px; top: 70px;
    font-family: "Archivo Narrow", sans-serif; color: var(--ink);
    font-size: 18px; line-height: 1.55; letter-spacing: .3px;
    white-space: nowrap;
  }
  .contact .email { margin-top: 10px; }
  .side-band {
    position: absolute; right: 0; top: -9px;
    width: 118px; height: 557px; background: var(--band-black);
  }
  .side-band .decor {
    position: absolute; left: 14px; top: 40px;
    width: 90px; height: 110px;
    background: linear-gradient(160deg, var(--slate-light), var(--slate));
  }
</style>
</head>
<body>
  <div class="card">
    <div class="brand-mark">
      <div class="brand-square"></div>
      <div>PEARLWOOD<br>FRAMING WORKS</div>
    </div>

    <h1 class="company-name">
      <span>PEARLWOOD FRAMING</span>
      <span>WORKS</span>
    </h1>
    <div class="divider"></div>

    <div class="contact">
      <p>7732 FERNGLEN PASS LN AUSTIN, TX 78734</p>
      <p>(512)555-0193</p>
      <p class="email">PEARLWOODFRAMINGWORKS@MAILNEST.EXAMPLE</p>
    </div>

    <div class="side-band">
      <div class="decor" role="img" aria-label="Large company emblem decoration"></div>
    </div>
  </div>
</body>
</html>
```